PDF flyer for our companies' two main products: Food processing machines.

PDF flyer with showcasing two products. Flyer can be one page per product, or both products on the same page.

Product #1: Labeled "Ribbon blenders".
Showing a photo of the machine, and the details/features offered with that machine. Product description must also say: "Sizes available; 2 Cu Ft. - 450 Cu Ft."

Product #2: Labeled: " Auger hoppers / Screw feeders"
Showing a photo of the machine, and the details/features offered with that machine.

SEE UPLOADED IMAGES; "Ribbon Blenders EXAMPLE FLYER".
& "Auger Hoppers / Screw Conveyors EXAMPLE FLYER" for a rough idea of what we are looking for.

Target Market(s)

Copackers, Packing houses, Food manufacturers, protein powder producers,

Industry/Entity Type

Commercial Food processing / packing / mixing equipment

Font styles to use
Serif

Colors
0054AA
0677BA
7BADD7
CADEEF
E8F1F8

Requirements
Must have
• Company logo on top of flyer.
Nice to have
• I would like for the flyer to show some stock images of common ingredients, similar to the images uploaded.
Should not have
• Pictures with background. Backgrounds must be removed from provides photos. "clipping path"

```html
<!DOCTYPE html>
<html lang="en">
<head>
<meta charset="utf-8">
<title>Keelstone Equipment – Product Flyers</title>
<link href="https://fonts.googleapis.com/css2?family=Orbitron:wght@500;600&family=Roboto:wght@400;500&display=swap" rel="stylesheet">
<style>
  :root{
    --bg:#f5f5f5;
    --frame:#00aeef;
    --navy:#0054aa;
    --sky:#00aeef;
    --ink:#1c1c1c;
    --text:#333;
    --box-line:#b9cde3;
    --arc:#e6e6e6;
  }
  *{box-sizing:border-box;margin:0;padding:0}
  html,body{width:1200px;height:879px;overflow:hidden;background:var(--bg)}
  body{position:relative;font-family:"Roboto",Arial,sans-serif;color:var(--text)}
  .page{position:absolute;top:76px;width:514px;height:727px;background:#fff;border:8px solid var(--frame);box-shadow:0 2px 8px rgba(0,0,0,.12)}
  .page--auger{left:58px}
  .page--blender{left:627px}
  .page > *{position:absolute}
  .brand{left:0;right:0;top:22px;height:44px;display:flex;align-items:center;justify-content:center;gap:8px;
    font-family:"Orbitron",sans-serif;font-weight:600;font-size:22px;letter-spacing:2px;color:var(--ink)}
  .brand__dot{width:14px;height:14px;border-radius:50%;background:var(--ink)}
  .title{left:0;right:0;text-align:center;font-family:"Orbitron",sans-serif;font-weight:600;color:var(--ink);letter-spacing:.5px;font-size:14.5px;line-height:18px}
  .page--auger .title{top:90px}
  .page--blender .title{top:84px}
  .subtitle{left:0;right:0;top:104px;text-align:center;font-family:"Orbitron",sans-serif;font-weight:500;font-size:8.5px;line-height:10px;color:var(--sky);letter-spacing:.3px}
  .card{width:214px;border:1px solid var(--box-line);border-radius:6px;overflow:hidden;background:#fff}
  .card__head{height:30px;padding-left:18px;display:flex;align-items:center;font-family:"Orbitron",sans-serif;font-weight:500;font-size:11px;color:#fff;letter-spacing:.3px}
  .card--std .card__head{background:var(--navy)}
  .card--opt .card__head{background:var(--sky)}
  .card ul{list-style:none;padding:15px 4px 0 22px}
  .card li{position:relative;padding-left:16px}
  .card li::before{content:"";position:absolute;left:0;width:7px;height:7px;border:1px solid var(--navy);border-radius:50%;
    background:radial-gradient(circle,var(--navy) 0 1.3px,transparent 1.6px)}
  .page--auger .card{top:127px;height:171px}
  .page--auger .card li{font-size:8.6px;line-height:12px;margin-bottom:7.8px}
  .page--auger .card li::before{top:2.5px}
  .page--blender .card{top:128px;height:187px}
  .page--blender .card ul{padding-top:15px}
  .page--blender .card li{font-size:6.7px;line-height:9px;margin-bottom:5.7px}
  .page--blender .card li::before{top:1px}
  .card li.nowrap{white-space:nowrap}
  .card--std{left:22px}
  .card--opt{left:263px}
  .ring{left:0;top:0;width:498px;height:711px;pointer-events:none}
  .machine{border-radius:8px}
  .page--auger .machine{left:96px;top:315px;width:205px;height:189px;
    background:linear-gradient(160deg,#d9dcdf,#9ea4aa 60%,#c7cacd)}
  .page--blender .machine{left:88px;top:371px;width:160px;height:167px;
    background:linear-gradient(160deg,#e1e3e5,#a2a7ac 60%,#c5c8cb)}
  .ingredient{width:64px;height:64px;border-radius:50%;border:1px solid #e4e4e4;margin:-32px 0 0 -32px}
  .spec{border-collapse:collapse;color:#000}
  .spec td{border:1px solid #000;padding:0 2px;white-space:nowrap}
  .page--auger .spec{left:95px;top:606px;width:309px;font-size:6px;border:1.5px solid #000}
  .page--auger .spec td{height:9.4px;line-height:8px}
  .page--auger .spec .c{text-align:center}
  .page--blender .spec{left:95px;top:594px;width:306px;font-size:3.8px;border:1px solid #999}
  .page--blender .spec td{height:6.9px;line-height:5.5px;border:.5px solid #aaa;padding:0 1px}
  .page--blender .spec tr:first-child td,.page--blender .spec td:first-child{font-weight:500}
  .folio{right:14px;bottom:8px;font-size:7px;color:#666}
</style>
</head>
<body>

<section class="page page--auger">
  <div class="brand"><span class="brand__dot"></span>KEELSTONE</div>
  <h1 class="title">AUGER HOPPERS / SCREW CONVEYORS</h1>

  <div class="card card--std">
    <div class="card__head">STANDARD FEATURES</div>
    <ul>
      <li>Direct Drive</li>
      <li>304 Stainless Steel Construction</li>
      <li>Stainless Steel Safety grating</li>
      <li>Pre-wired control panel</li>
      <li>Electric Vibrator</li>
      <li>Castor Wheels</li>
    </ul>
  </div>
  <div class="card card--opt">
    <div class="card__head">OPTIONS</div>
    <ul>
      <li>Square or round hopper 3.5cf and 7cf hopper are standard</li>
      <li>Custom hoppers upto 200cf</li>
      <li>VFD (Variable Frequency Drive)</li>
      <li>Clamshell Auger Tube for easy cleanout</li>
      <li>316 Stainless Steel Construction</li>
    </ul>
  </div>

  <svg class="ring" viewBox="0 0 498 711" aria-hidden="true">
    <path d="M236 390 A120 120 0 0 1 376 470 A120 120 0 0 1 236 555" fill="none" stroke="var(--arc)" stroke-width="1"/>
  </svg>
  <div class="machine" role="img" aria-label="Stainless steel auger hopper with inclined screw conveyor on castor wheels"></div>
  <div class="ingredient" style="left:285px;top:346px;background:radial-gradient(circle,#3a332d 0 40%,#fff 62%)" role="img" aria-label="Black peppercorns"></div>
  <div class="ingredient" style="left:361px;top:388px;background:radial-gradient(circle,#9a9a55 0 38%,#fff 62%)" role="img" aria-label="Green cardamom pods"></div>
  <div class="ingredient" style="left:376px;top:470px;background:radial-gradient(circle,#8b4a24 0 38%,#fff 62%)" role="img" aria-label="Cinnamon sticks and ground cinnamon"></div>
  <div class="ingredient" style="left:329px;top:543px;background:radial-gradient(circle,#6e3418 0 38%,#fff 62%)" role="img" aria-label="Star anise"></div>
  <div class="ingredient" style="left:236px;top:555px;background:radial-gradient(circle,#e3cf9a 0 38%,#fff 62%)" role="img" aria-label="Fresh ginger root"></div>

  <table class="spec">
    <tr><td>MODEL</td><td>AH-A2</td><td>AH-A3</td><td>AH-A5</td><td>AH-A7</td><td>AH-A8</td><td>AH-A12</td></tr>
    <tr><td>FEEDING RATE</td><td>2m³/Hr</td><td>3m³/Hr</td><td>5m³/Hr</td><td>7m³/Hr</td><td>8m³/Hr</td><td>12m³/Hr</td></tr>
    <tr><td>PIPE DIAMETER</td><td>4"</td><td>4-1/2"</td><td>5-1/2"</td><td>6-1/4"</td><td>6-1/2"</td><td>8-1/2"</td></tr>
    <tr><td>HOPPER VOL.</td><td>3.5CF</td><td class="c" colspan="5">7CF</td></tr>
    <tr><td>DIMENSIONS</td><td>28.6"x24.4"x31.5"</td><td class="c" colspan="5">40" x 32" x 35"</td></tr>
    <tr><td>TOTAL WEIGHT</td><td>221LBS</td><td>287LBS</td><td>397LBS</td><td>441LBS</td><td>485LBS</td><td>596LBS</td></tr>
    <tr><td>CHARGING HEIGHT</td><td class="c" colspan="6">STANDARD 72 INCHES. (40" - 196" AVAILABLE)</td></tr>
    <tr><td>CHARGING ANGLE</td><td class="c" colspan="6">STANDARD 45° (30°-60° AVAILABLE)</td></tr>
  </table>
  <div class="folio">C2</div>
</section>

<section class="page page--blender">
  <div class="brand"><span class="brand__dot"></span>KEELSTONE</div>
  <h1 class="title">RIBBON BLENDERS</h1>
  <p class="subtitle">SIZES AVAILABLE; 2 CU FT. - 450 CU FT</p>

  <div class="card card--std">
    <div class="card__head">STANDARD FEATURES</div>
    <ul>
      <li>304 Stainless Steel Construction</li>
      <li>Pre-wired control panel with; batch timer, on/off<br>switch, emergency stop button</li>
      <li>Food grade compression shaft seals</li>
      <li class="nowrap">Safety sensor on lid for automatic shutoff when opened</li>
      <li>Air acutated discharge valve</li>
      <li>1 Piece hinged lid with safety granting</li>
      <li>Power options; 220v/480v</li>
      <li>24" Standard discharge height</li>
      <li>Castor wheels on 53cf units and smaller</li>
    </ul>
  </div>
  <div class="card card--opt">
    <div class="card__head">OPTIONS</div>
    <ul>
      <li>Dual hinged lids available on custom order</li>
      <li class="nowrap">knife gate style discharge available on custom orders</li>
      <li>Air pure seals available on custom orders</li>
      <li>316 Stainless materials avaiable on custom orders</li>
      <li>custom height modification</li>
      <li>liquid spary systems</li>
      <li>(VFD) Variable Frequency Drives</li>
      <li>Leg extensions</li>
    </ul>
  </div>

  <svg class="ring" viewBox="0 0 498 711" aria-hidden="true">
    <path d="M231 400 A120 120 0 0 1 366 475 A120 120 0 0 1 231 559" fill="none" stroke="var(--arc)" stroke-width="1"/>
  </svg>
  <div class="machine" role="img" aria-label="Stainless steel ribbon blender with side control panel on a wheeled frame"></div>
  <div class="ingredient" style="left:278px;top:357px;background:radial-gradient(circle,#c23a22 0 38%,#fff 62%)" role="img" aria-label="Red chili powder and dried chilies"></div>
  <div class="ingredient" style="left:352px;top:397px;background:radial-gradient(circle,#5a4636 0 38%,#fff 62%)" role="img" aria-label="Peppercorns and chia seeds"></div>
  <div class="ingredient" style="left:366px;top:475px;background:radial-gradient(circle,#8d7d52 0 38%,#fff 62%)" role="img" aria-label="Cumin seeds and ground spice"></div>
  <div class="ingredient" style="left:321px;top:546px;background:radial-gradient(circle,#e8a21a 0 38%,#fff 62%)" role="img" aria-label="Turmeric powder and root"></div>
  <div class="ingredient" style="left:231px;top:559px;background:radial-gradient(circle,#b27a52 0 38%,#fff 62%)" role="img" aria-label="Ground coriander in a bowl"></div>

  <table class="spec">
    <tr><td>Model Size</td><td>5cf</td><td>7CF</td><td>10.5CF</td><td>17.5CF</td><td>35CF</td><td>53CF</td><td>70.5CF</td><td>106CF</td></tr>
    <tr><td>Working Liters</td><td>120L</td><td>200L</td><td>300L</td><td>500L</td><td>1000L</td><td>1500L</td><td>2000L</td><td>3000L</td></tr>
    <tr><td>Fill Capcity</td><td>5CF / 150L</td><td>9CF / 250L</td><td>13CF / 375L</td><td>22CF / 625L</td><td>44CF / 1250L</td><td>66CF / 1875L</td><td>88CF / 2500L</td><td>132CF / 3750L</td></tr>
    <tr><td>Weight</td><td>440lbs</td><td>550lbs</td><td>770lbs</td><td>1212lbs</td><td>1874lbs</td><td>2645lbs</td><td>3527lbs</td><td>5511lbs</td></tr>
    <tr><td>Motor Size</td><td>4hp</td><td>5.3hp</td><td>6.7hp</td><td>10hp</td><td>14.75hp</td><td>20hp</td><td>25hp</td><td>30hp</td></tr>
    <tr><td>Total Length</td><td>50"</td><td>53.5"</td><td>63"</td><td>72"</td><td>94"</td><td>102"</td><td>131.5"</td><td>157.5"</td></tr>
    <tr><td>Total Width</td><td>28"</td><td>34"</td><td>41.5"</td><td>45"</td><td>52"</td><td>66"</td><td>52.5"</td><td>54"</td></tr>
    <tr><td>Total Height</td><td>66"</td><td>69"</td><td>71"</td><td>82"</td><td>87"</td><td>95"</td><td>76"</td><td>110"</td></tr>
    <tr><td>Tub Length</td><td>31.5"</td><td>35.5"</td><td>41"</td><td>47"</td><td>59"</td><td>70"</td><td>75"</td><td>100"</td></tr>
    <tr><td>Tub Width</td><td>16.5"</td><td>22"</td><td>25"</td><td>27.5"</td><td>35.5"</td><td>39"</td><td>48"</td><td>48"</td></tr>
    <tr><td>Tub Height</td><td>20.5"</td><td>26"</td><td>28"</td><td>33"</td><td>41"</td><td>46"</td><td>51"</td><td>53"</td></tr>
    <tr><td>Shaft Diameter</td><td>2"</td><td>2-1/4"</td><td>2-5/8"</td><td>3"</td><td>3.5"</td><td>4"</td><td>4"</td><td>5-1/4"</td></tr>
    <tr><td>Tub Thickness</td><td>3mm</td><td>3mm</td><td>3mm</td><td>4mm</td><td>4mm</td><td>5mm</td><td>5mm</td><td>6mm</td></tr>
    <tr><td>Ribbon Thickness</td><td>6mm</td><td>8mm</td><td>8mm</td><td>8mm</td><td>10mm</td><td>12mm</td><td>12mm</td><td>14mm</td></tr>
    <tr><td>Max RPM</td><td>46 rpm</td><td>46 rpm</td><td>46 rpm</td><td>46 rpm</td><td>30 rpm</td><td>31 rpm</td><td>32 rpm</td><td>33 rpm</td></tr>
  </table>
  <div class="folio">C2</div>
</section>

</body>
</html>
```